Velmor Spire Nine Flash website

we need a website to cater to 2 aspect of the business. We have Velmor spire residence and velmor spire office. For the office, we will get their inquire and arrange a face to face meetup to show them the office area for rent. For the residence side, it will need to be like staylane or roomvio.com. we want to allow them to book online for the date they need. We have a total of 10 different room configurations starting at $70 per night and up depending on the size of the room. example of the design is https://brisquelodge.com/

Target Market(s)

the website should have detail information on the layout, designs, and luxury of the building.

Industry/Entity Type

office and service appartment rental/lease

Coding

Coded - Design and coding required

Number of Pages Required

5+ page

Requirements
Must have
• a luxury perspective
Nice to have
• example https://brisquelodge.com/

```html
<!DOCTYPE html>
<html lang="en">
<head>
<meta charset="utf-8">
<title>Velmor Spire Nine</title>
<link href="https://fonts.googleapis.com/css2?family=Marcellus&family=Oswald:wght@300;400&family=Roboto:wght@400;500&display=swap" rel="stylesheet">
<style>
:root{
  --gold:#d29a2a;
  --cream:#fdf1dc;
  --ink:#111;
  --text:#333;
  --muted:#777;
  --board:#d3d3d3;
  --line:#e2e2e2;
  --price:#d1502f;
  --white:#fff;
}
*{box-sizing:border-box;margin:0;padding:0}
html,body{width:1200px;height:4405px;overflow:hidden}
body{background:var(--board);font-family:"Roboto",Arial,sans-serif;color:var(--text);position:relative}
.page{position:absolute;left:75px;width:1056px;background:var(--white);overflow:hidden}
.page--landing{top:75px;height:1255px}
.page--home{top:1388px;height:2958px}
.abs{position:absolute}

/* nav */
.nav{position:absolute;left:0;top:0;width:100%;height:63px;background:var(--white);z-index:3}
.nav a{position:absolute;top:22px;font-size:14px;font-weight:500;color:var(--ink);text-decoration:none;transform:translateX(-50%)}
.nav .login{left:858px;top:17px;width:101px;height:31px;border-radius:16px;background:var(--gold);color:var(--white);text-align:center;line-height:31px;transform:none}
.brand-badge{position:absolute;left:443px;top:-38px;width:170px;height:170px;border-radius:50%;background:var(--white);z-index:4;display:flex;align-items:flex-end;justify-content:center;padding-bottom:30px}
.brand-badge span{font-family:"Marcellus",serif;font-size:15px;color:#8a6a2c;letter-spacing:.5px}

/* hero */
.hero{position:absolute;left:0;top:63px;width:100%;height:566px}
.hero__office{position:absolute;left:0;top:0;width:50%;height:100%;background:linear-gradient(180deg,#3a2c22 0%,#5a4230 14%,#4b4c52 30%,#6a6b6e 55%,#8c8378 78%,#b7a58c 100%)}
.hero__room{position:absolute;right:0;top:0;width:50%;height:100%;background:linear-gradient(180deg,#6f7278 0%,#777a80 35%,#8b8a88 58%,#c9c3b8 72%,#76716b 86%,#5a5855 100%)}
.hero__shade{position:absolute;inset:0;background:rgba(20,20,25,.22)}
.hero__copy{position:absolute;left:0;width:100%;text-align:center;color:var(--white);font-family:"Marcellus",serif}
.hero__kicker{font-size:30px;letter-spacing:1px}
.hero__title{font-size:64px;line-height:1;letter-spacing:1px;margin-top:6px}
.btn{display:inline-block;background:var(--gold);color:var(--white);font-family:"Roboto",Arial,sans-serif;font-weight:500;font-size:14px;border-radius:17px;height:34px;line-height:34px;padding:0 12px}

/* landing cards */
.portal{position:absolute;top:713px;width:420px;height:372px;border:1px solid var(--line);background:var(--white);box-shadow:0 1px 3px rgba(0,0,0,.12)}
.portal__photo{height:290px}
.portal__label{height:82px;padding:0 20px;display:flex;align-items:center;font-family:"Oswald",sans-serif;font-weight:300;font-size:22px;text-transform:uppercase;letter-spacing:.5px}
.portal--residence .portal__label{background:var(--gold);color:var(--white)}
.portal--office .portal__label{color:var(--ink)}
.corner-icon{position:absolute;right:0;bottom:0;width:32px;height:32px;border-radius:50% 0 0 0;background:var(--ink)}

/* simple footer */
.footbar{position:absolute;left:0;top:1169px;width:100%;height:86px;background:#000;color:var(--white);font-size:13px;font-weight:500}
.footbar a{position:absolute;top:34px;color:var(--white);text-decoration:none}
.footbar .copy{position:absolute;right:97px;top:34px;font-weight:400}

/* search */
.search{position:absolute;left:98px;top:478px;width:861px;height:294px;background:var(--white);border-radius:14px;box-shadow:0 2px 8px rgba(0,0,0,.15);z-index:2}
.tab{position:absolute;top:32px;height:34px;border-radius:17px;font-size:14px;font-weight:500;text-align:center;line-height:32px;border:1.5px solid var(--gold)}
.tab--on{background:var(--gold);color:var(--white)}
.tab--off{color:var(--ink);background:var(--white)}
.field{position:absolute;border:1px solid var(--line);border-radius:6px;background:#f6f6f6;font-size:13px;color:#444}
.field--dest{left:37px;top:87px;width:781px;height:72px;display:flex;align-items:center;padding-left:18px;gap:10px}
.field--dates{left:37px;top:180px;width:330px;height:71px}
.field--guests{left:379px;top:180px;width:164px;height:71px}
.date{position:absolute;top:22px;display:flex;gap:6px;align-items:flex-start}
.date b{font-weight:500;font-size:13px;display:block;line-height:14px}
.date i{font-style:normal;color:var(--muted);font-size:12px;display:block;line-height:13px}
.search__go{position:absolute;left:564px;top:180px;width:176px;height:71px;background:var(--gold);color:var(--white);border-radius:4px;font-size:22px;font-weight:500;text-align:center;line-height:71px}

/* rooms */
.room{position:absolute;width:225px;font-size:13px;line-height:24px;color:var(--ink);white-space:nowrap}
.room__photo{width:205px;height:155px;margin-bottom:10px}
.room__loc{display:flex;align-items:center;gap:4px}
.room__price{color:var(--price);font-size:17px;margin-top:2px}

/* about */
.about{position:absolute;left:0;top:1562px;width:100%;height:511px;background:var(--cream)}
.about__photo{position:absolute;left:0;top:0;width:489px;height:100%;background:linear-gradient(90deg,#4a3a30 0%,#7b6656 18%,#c9a27a 38%,#e9e4dc 58%,#f3f0ea 72%,#a89d90 88%,#6e5e50 100%)}
.about__body{position:absolute;left:532px;top:62px;width:430px}
.h2{font-family:"Marcellus",serif;font-size:38px;color:var(--ink);letter-spacing:1px;font-weight:400}
.about__body p{font-size:13px;line-height:24px;color:#333;margin-top:14px}

/* reviews */
.reviews__title{position:absolute;left:0;top:2150px;width:100%;text-align:center}
.review{position:absolute;top:2264px;width:265px;height:284px;border:1px solid #ddd;background:var(--white);padding:60px 14px 0 14px;font-size:13px;line-height:23px;text-align:justify;box-shadow:0 1px 3px rgba(0,0,0,.1)}
.review--featured{background:var(--gold);border-color:var(--gold)}
.review__name{font-family:"Marcellus",serif;font-size:18px;color:var(--gold);margin-bottom:4px;text-transform:uppercase}
.review--featured .review__name{color:var(--ink)}
.avatar{position:absolute;top:-22px;left:2px;width:76px;height:76px;border-radius:50%;border:3px solid var(--white);background:linear-gradient(160deg,#d8cfc6,#8d8178)}
.arrow{position:absolute;top:2379px;width:32px;height:32px;border-radius:50%;display:flex;align-items:center;justify-content:center}
.arrow--prev{left:47px;background:#000}
.arrow--next{left:982px;background:#777}

/* footer */
.footer{position:absolute;left:0;top:2633px;width:100%;height:325px;background:#111;color:var(--white)}
.footer h3{font-family:"Marcellus",serif;font-weight:400;font-size:24px;letter-spacing:1px}
.footer__links{position:absolute;left:161px;top:50px}
.footer__links a{display:block;color:var(--white);text-decoration:none;font-size:13px;font-weight:500;margin-top:19px}
.footer__brand{position:absolute;left:250px;top:215px;width:460px;text-align:center;font-family:"Marcellus",serif;font-size:40px;color:var(--gold)}
.footer__copy{position:absolute;left:250px;top:288px;width:460px;text-align:center;font-size:12px}
.footer__contact{position:absolute;left:713px;top:50px}
.contact-row{display:flex;align-items:center;gap:10px;font-size:13px;margin-top:20px}
.contact-row .dot{width:36px;height:36px;border-radius:50%;background:var(--gold);display:flex;align-items:center;justify-content:center}
</style>
</head>
<body>

<!-- Landing page -->
<section class="page page--landing">
  <nav class="nav">
    <a style="left:118px">Home</a><a style="left:224px">Location</a><a style="left:344px">Experience</a>
    <a style="left:648px">About Us</a><a style="left:776px">Contact Us</a>
    <a class="login">Login</a>
  </nav>
  <div class="brand-badge"><span>Velmor Spire Nine</span></div>
  <header class="hero">
    <div class="hero__office" role="img" aria-label="Modern office workspace with desks and wood ceiling"></div>
    <div class="hero__room" role="img" aria-label="Luxury bedroom with chandelier and grey panelled walls"></div>
    <div class="hero__shade"></div>
    <div class="hero__copy" style="top:243px">
      <div class="hero__kicker">WELCOME TO</div>
      <div class="hero__title">VELMOR SPIRE NINE</div>
      <div style="margin-top:10px"><span class="btn">Get Started</span></div>
    </div>
  </header>

  <article class="portal portal--residence" style="left:98px">
    <div class="portal__photo" role="img" aria-label="Bright bedroom with white bedding and seascape painting" style="background:linear-gradient(180deg,#e9ecec 0%,#a9c3c6 25%,#d7dcdc 45%,#b9c6c8 62%,#f1f2f0 78%,#9aa7aa 100%)"></div>
    <div class="portal__label">Velmor Spire Residence</div>
  </article>
  <article class="portal portal--office" style="left:539px">
    <div class="portal__photo" role="img" aria-label="Open plan office with workstations and orange accent wall" style="background:linear-gradient(180deg,#f4f5f7 0%,#e3e6ea 30%,#d98a45 42%,#c9ced4 50%,#8f99a5 68%,#4b5566 84%,#6a7a9a 100%)"></div>
    <div class="portal__label">Velmor Spire Office</div>
    <span class="corner-icon"></span>
  </article>

  <footer class="footbar">
    <a style="left:98px">Home</a><a style="left:165px">Location</a><a style="left:250px">Experience</a><a style="left:350px">About Us</a><a style="left:438px">Contact Us</a>
    <span class="copy">Copyright © 2024 Velmor Spire Nine | All Rights Reserved</span>
  </footer>
</section>

<!-- Home page -->
<section class="page page--home">
  <nav class="nav">
    <a style="left:118px">Home</a><a style="left:224px">Location</a><a style="left:344px">Experience</a>
    <a style="left:648px">About Us</a><a style="left:776px">Contact Us</a>
    <a class="login">Login</a>
  </nav>
  <div class="brand-badge"><span>Velmor Spire Nine</span></div>
  <header class="hero" style="height:567px">
    <div class="hero__office" role="img" aria-label="Modern office workspace with desks and wood ceiling"></div>
    <div class="hero__room" role="img" aria-label="Luxury bedroom with chandelier and grey panelled walls"></div>
    <div class="hero__shade"></div>
    <div class="hero__copy" style="top:168px">
      <div class="hero__kicker">WELCOME TO</div>
      <div class="hero__title">VELMOR SPIRE NINE</div>
      <div style="margin-top:10px"><span class="btn">Get Started</span></div>
    </div>
  </header>

  <form class="search">
    <span class="tab tab--on" style="left:37px;width:133px">Overnight Stays</span>
    <span class="tab tab--off" style="left:182px;width:132px">Day Use Stays</span>
    <div class="field field--dest">
      <svg width="16" height="16" viewBox="0 0 16 16"><circle cx="7" cy="7" r="5" fill="none" stroke="#999" stroke-width="1.5"/><line x1="11" y1="11" x2="15" y2="15" stroke="#999" stroke-width="1.5"/></svg>
      Enter a Destination&nbsp; Or&nbsp; Property
    </div>
    <div class="field field--dates">
      <div class="date" style="left:16px">
        <svg width="18" height="18" viewBox="0 0 18 18"><rect x="1.5" y="3" width="15" height="13" rx="1.5" fill="none" stroke="#777" stroke-width="1.4"/><line x1="1.5" y1="7" x2="16.5" y2="7" stroke="#777" stroke-width="1.4"/><line x1="5" y1="1" x2="5" y2="4" stroke="#777" stroke-width="1.4"/><line x1="13" y1="1" x2="13" y2="4" stroke="#777" stroke-width="1.4"/></svg>
        <span><b>19 May 2024</b><i>&nbsp;Monday</i></span>
      </div>
      <div class="date" style="left:160px;border-left:1px solid #ccc;padding-left:8px">
        <svg width="18" height="18" viewBox="0 0 18 18"><rect x="1.5" y="3" width="15" height="13" rx="1.5" fill="none" stroke="#777" stroke-width="1.4"/><line x1="1.5" y1="7" x2="16.5" y2="7" stroke="#777" stroke-width="1.4"/><line x1="5" y1="1" x2="5" y2="4" stroke="#777" stroke-width="1.4"/><line x1="13" y1="1" x2="13" y2="4" stroke="#777" stroke-width="1.4"/></svg>
        <span><b>20 May 2024</b><i>&nbsp;Monday</i></span>
      </div>
    </div>
    <div class="field field--guests">
      <div class="date" style="left:16px;top:20px">
        <svg width="32" height="22" viewBox="0 0 32 22"><circle cx="10" cy="7" r="5" fill="none" stroke="#555" stroke-width="1.4"/><path d="M1 21c0-5 4-8 9-8s9 3 9 8" fill="none" stroke="#555" stroke-width="1.4"/><circle cx="21" cy="7" r="5" fill="none" stroke="#555" stroke-width="1.4"/><path d="M17 13c1-.3 2-.4 4-.4 5 0 9 3 9 8" fill="none" stroke="#555" stroke-width="1.4"/></svg>
        <span><b>2 Adult</b><b style="font-weight:400">1 Room</b></span>
      </div>
    </div>
    <span class="search__go">Search</span>
  </form>

  <!-- rooms grid -->
  <div class="room" style="left:98px;top:858px"><div class="room__photo" role="img" aria-label="Minimal grey bedroom with city window" style="background:linear-gradient(180deg,#e6e5e2 0%,#9b9893 35%,#6e6a66 55%,#e8e6e2 70%,#4f4c49 100%)"></div>Lorem ipsum dolor sit t,consectet<br>adipiscing elit, sed gravida.<div class="room__loc"><svg width="9" height="12" viewBox="0 0 9 12"><path d="M4.5 0a4.5 4.5 0 0 1 4.5 4.5C9 8 4.5 12 4.5 12S0 8 0 4.5A4.5 4.5 0 0 1 4.5 0z" fill="#d1502f"/><circle cx="4.5" cy="4.5" r="1.6" fill="#fff"/></svg>Lorem ipsum dolor sit</div><div class="room__price">$70.00 / night</div></div>
  <div class="room" style="left:316px;top:858px"><div class="room__photo" role="img" aria-label="Warm wood panelled bedroom with pendant lights" style="background:linear-gradient(180deg,#6f5846 0%,#a98a6c 30%,#d9c6ae 52%,#8a7260 70%,#efe6da 82%,#5b4839 100%)"></div>Lorem ipsum dolor sit t,consectet<br>adipiscing elit, sed gravida.<div class="room__loc"><svg width="9" height="12" viewBox="0 0 9 12"><path d="M4.5 0a4.5 4.5 0 0 1 4.5 4.5C9 8 4.5 12 4.5 12S0 8 0 4.5A4.5 4.5 0 0 1 4.5 0z" fill="#d1502f"/><circle cx="4.5" cy="4.5" r="1.6" fill="#fff"/></svg>Lorem ipsum dolor sit</div><div class="room__price">$80.00 / night</div></div>
  <div class="room" style="left:535px;top:858px"><div class="room__photo" role="img" aria-label="Light bedroom with large window and white bedding" style="background:linear-gradient(180deg,#f3f1ec 0%,#cfc6b8 30%,#e9e4dc 50%,#b7ab9a 62%,#fbfaf7 78%,#a89a86 100%)"></div>Lorem ipsum dolor sit t,consectet<br>adipiscing elit, sed gravida.<div class="room__loc"><svg width="9" height="12" viewBox="0 0 9 12"><path d="M4.5 0a4.5 4.5 0 0 1 4.5 4.5C9 8 4.5 12 4.5 12S0 8 0 4.5A4.5 4.5 0 0 1 4.5 0z" fill="#d1502f"/><circle cx="4.5" cy="4.5" r="1.6" fill="#fff"/></svg>Lorem ipsum dolor sit</div><div class="room__price">$100.00 / night</div></div>
  <div class="room" style="left:754px;top:858px"><div class="room__photo" role="img" aria-label="Twin bed room with brown throws" style="background:linear-gradient(180deg,#dcdad6 0%,#8f8a84 30%,#5e5450 48%,#ece8e2 62%,#7d6656 80%,#c9c1b6 100%)"></div>Lorem ipsum dolor sit t,consectetur<br>adipiscing elit, sed gravida.<div class="room__loc"><svg width="9" height="12" viewBox="0 0 9 12"><path d="M4.5 0a4.5 4.5 0 0 1 4.5 4.5C9 8 4.5 12 4.5 12S0 8 0 4.5A4.5 4.5 0 0 1 4.5 0z" fill="#d1502f"/><circle cx="4.5" cy="4.5" r="1.6" fill="#fff"/></svg>Lorem ipsum dolor sit</div><div class="room__price">$90.00 / night</div></div>

  <div class="room" style="left:98px;top:1160px"><div class="room__photo" role="img" aria-label="Bedroom with city view and desk" style="background:linear-gradient(180deg,#f0efed 0%,#8f9297 30%,#6f6c69 48%,#e7e4df 64%,#b8b1a8 82%,#d9d5cf 100%)"></div>Lorem ipsum dolor sit t,consectet<br>adipiscing elit, sed gravida.<div class="room__loc"><svg width="9" height="12" viewBox="0 0 9 12"><path d="M4.5 0a4.5 4.5 0 0 1 4.5 4.5C9 8 4.5 12 4.5 12S0 8 0 4.5A4.5 4.5 0 0 1 4.5 0z" fill="#d1502f"/><circle cx="4.5" cy="4.5" r="1.6" fill="#fff"/></svg>Lorem ipsum dolor sit</div><div class="room__price">$120.00 / night</div></div>
  <div class="room" style="left:316px;top:1160px"><div class="room__photo" role="img" aria-label="Dark moody bedroom with low bed" style="background:linear-gradient(180deg,#3a322e 0%,#4d423c 35%,#6a5d55 55%,#8c7d73 70%,#4a3f3a 86%,#2f2926 100%)"></div>Lorem ipsum dolor sit t,consectet<br>adipiscing elit, sed gravida.<div class="room__loc"><svg width="9" height="12" viewBox="0 0 9 12"><path d="M4.5 0a4.5 4.5 0 0 1 4.5 4.5C9 8 4.5 12 4.5 12S0 8 0 4.5A4.5 4.5 0 0 1 4.5 0z" fill="#d1502f"/><circle cx="4.5" cy="4.5" r="1.6" fill="#fff"/></svg>Lorem ipsum dolor sit</div><div class="room__price">$110.00 / night</div></div>
  <div class="room" style="left:535px;top:1160px"><div class="room__photo" role="img" aria-label="Blue toned night bedroom with skyline window" style="background:linear-gradient(180deg,#1f2733 0%,#3c4a5e 30%,#6f7c8e 48%,#a38f70 62%,#4a4d55 80%,#23262c 100%)"></div>Lorem ipsum dolor sit t,consectet<br>adipiscing elit, sed gravida.<div class="room__loc"><svg width="9" height="12" viewBox="0 0 9 12"><path d="M4.5 0a4.5 4.5 0 0 1 4.5 4.5C9 8 4.5 12 4.5 12S0 8 0 4.5A4.5 4.5 0 0 1 4.5 0z" fill="#d1502f"/><circle cx="4.5" cy="4.5" r="1.6" fill="#fff"/></svg>Lorem ipsum dolor sit</div><div class="room__price">$130.00 / night</div></div>
  <div class="room" style="left:754px;top:1160px"><div class="room__photo" role="img" aria-label="Classic white bedroom with chandelier" style="background:linear-gradient(180deg,#f5f2ee 0%,#e2d9cc 30%,#c8b89e 45%,#f1ece5 62%,#d6cbbd 80%,#b9ad9e 100%)"></div>Lorem ipsum dolor sit t,consectetur<br>adipiscing elit, sed gravida.<div class="room__loc"><svg width="9" height="12" viewBox="0 0 9 12"><path d="M4.5 0a4.5 4.5 0 0 1 4.5 4.5C9 8 4.5 12 4.5 12S0 8 0 4.5A4.5 4.5 0 0 1 4.5 0z" fill="#d1502f"/><circle cx="4.5" cy="4.5" r="1.6" fill="#fff"/></svg>Lorem ipsum dolor sit</div><div class="room__price">$140.00 / night</div></div>

  <div class="abs" style="left:0;top:1449px;width:100%;text-align:center"><span class="btn" style="padding:0 14px">View More</span></div>

  <section class="about">
    <div class="about__photo" role="img" aria-label="Traveller with suitcase by a hotel room window"></div>
    <div class="about__body">
      <h2 class="h2">ABOUT US</h2>
      <p style="margin-top:16px">Lorem ipsum dolor sit amet, consectetur adipiscing elit, sed do iusmod tempor incididunt ut labore et dolore magna aliqua. Ut enim ad minim iam, quis nostrud exercitation ullamco laboris nisi ut aliquip ex mmodo consequat. Duis aute irure dolor in reprehenderit in voluptate velit esse cillum dolore eu fugiat nulla pariatur. Excepteur sint occaecat cupidatat non proident, sunt in culpa qui officia deserunt mollit anim id est orum."</p>
      <p>Lorem ipsum dolor sit amet, consectetur adipiscing elit, sed do iusmod tempor incididunt ut labore et dolore magna aliqua. Ut enim ad minim iam, quis nostrud exercitation ullamco laboris nisi ut aliquip ex mmodo consequat. Duis aute irure dolor in reprehenderit in voluptate velit esse cillum dolore eu fugiat nulla pariatur.</p>
      <div style="margin-top:12px"><span class="btn">Learn More</span></div>
    </div>
  </section>

  <h2 class="h2 reviews__title">OUR REVIEWS</h2>
  <span class="arrow arrow--prev"><svg width="12" height="12" viewBox="0 0 12 12"><path d="M8 1L3 6l5 5" fill="none" stroke="#fff" stroke-width="2"/></svg></span>
  <span class="arrow arrow--next"><svg width="12" height="12" viewBox="0 0 12 12"><path d="M4 1l5 5-5 5" fill="none" stroke="#fff" stroke-width="2"/></svg></span>
  <article class="review" style="left:101px"><span class="avatar" role="img" aria-label="Reviewer portrait"></span><div class="review__name">Aaron Whitby</div>Lorem ipsum dolor sit amet, piscing elit, d do eiusmod tempor incididunt ut labore et dolore magna aliqua. Quis ipsum pendisse accumsan lacus vel facilisis. Lorem lor sit amet, nsectetur adipiscing elit, sed doe mod tempor incididunt ut labore remagna aliqua facilisis....</article>
  <article class="review review--featured" style="left:397px"><span class="avatar" role="img" aria-label="Reviewer portrait"></span><div class="review__name">Lena</div>Lorem ipsum dolor sit amet, piscing elit, d do eiusmod tempor incididunt ut labore et dolore magna aliqua. Quis ipsum pendisse accumsan lacus vel facilisis. Lorem lor sit amet, nsectetur adipiscing elit, sed doe mod tempor incididunt ut labore remagna aliqua facilisis....</article>
  <article class="review" style="left:692px"><span class="avatar" role="img" aria-label="Reviewer portrait"></span><div class="review__name">Corwin</div>Lorem ipsum dolor sit amet, piscing elit, d do eiusmod tempor incididunt ut labore et dolore magna aliqua. Quis ipsum pendisse accumsan lacus vel facilisis. Lorem lor sit amet, nsectetur adipiscing elit, sed doe mod tempor incididunt ut labore remagna aliqua facilisis...</article>

  <footer class="footer">
    <div class="footer__links">
      <h3>QUICK LINKS</h3>
      <a>Home</a><a>Location</a><a>Experience</a><a>About Us</a><a style="margin-left:4px">Contact Us</a>
    </div>
    <div class="footer__brand">Velmor Spire Nine</div>
    <div class="footer__copy">Copyright © 2024 Velmor Spire Nine | All Rights Reserved</div>
    <div class="footer__contact">
      <h3>CONTACT US</h3>
      <div class="contact-row"><span class="dot"><svg width="16" height="12" viewBox="0 0 16 12"><rect width="16" height="12" rx="1.5" fill="#fff"/><path d="M1 1l7 5 7-5" fill="none" stroke="#d29a2a" stroke-width="1.4"/></svg></span>info@velmorspirenine</div>
      <div class="contact-row" style="margin-top:24px"><span class="dot"><svg width="15" height="15" viewBox="0 0 24 24"><path d="M6.6 10.8a15 15 0 0 0 6.6 6.6l2.2-2.2a1 1 0 0 1 1-.25 11.4 11.4 0 0 0 3.6.57 1 1 0 0 1 1 1V20a1 1 0 0 1-1 1A17 17 0 0 1 3 4a1 1 0 0 1 1-1h3.5a1 1 0 0 1 1 1c0 1.25.2 2.45.57 3.6a1 1 0 0 1-.25 1z" fill="#fff"/></svg></span>+1(555)010 2040</div>
      <div class="contact-row" style="margin-top:24px"><span class="dot"><svg width="12" height="16" viewBox="0 0 9 12"><path d="M4.5 0a4.5 4.5 0 0 1 4.5 4.5C9 8 4.5 12 4.5 12S0 8 0 4.5A4.5 4.5 0 0 1 4.5 0z" fill="#fff"/><circle cx="4.5" cy="4.5" r="1.6" fill="#d29a2a"/></svg></span>Lorem ipsum dolor,USA</div>
    </div>
  </footer>
</section>

</body>
</html>
```